Velmarsh Group Webpage Design

We need a new website for our company. The company is Velmarsh Group Pty Ltd. We are in the business of Asbestos Removal; Demolition; Earthworks and Transport. We do not advertise and would like our website to be a reference point for our clients / potential clients and also to make our services known to those searching the internet for the services we offer. Some examples of the style of website we are after are:
http://www.quarnedemolition-example.com.au/
http://m.brintowerdemolitions-example.com.au/
http://www.fenwarddemolition-example.com.au
http://www.tolvik-example.com.au
http://www.ptrservices-example.com.au
http://www.steadfast-dismantling-example.com.au
We will need to work on content. Enclosed is an example. We also need to purchase the domain velmarshgroup-example.com.au and need to set up email accounts and ensure the website is mobile friendly. We have a company logo and have built our business on delivering professional, quality services on time. We would like the webpage to be simple, informative and professional - black and white / grey themed. We would also like to add a photo gallery etc later.

Industry/Entity Type

Construction

Coding

Coded - Design and coding required

Number of Pages Required

1 page

Colors
000000
fcfcfc
959595
dddddd

Requirements
Must have
• Information regarding the services we provide

```html
<!DOCTYPE html>
<html lang="en">
<head>
<meta charset="utf-8">
<title>Velmarsh Group</title>
<link rel="stylesheet" href="https://fonts.googleapis.com/css2?family=Roboto:wght@300;400;500;700&display=swap">
<style>
:root{
  --black:#000000;
  --white:#fcfcfc;
  --grey:#959595;
  --light:#dddddd;
  --ink:#111111;
  --hero-a:#5a5a5a;
  --hero-b:#9a9a9a;
  --about-a:#2a2620;
  --about-b:#4a3f2c;
  --map:#d4d4d4;
}
*{margin:0;padding:0;box-sizing:border-box}
html,body{width:1200px;height:2381px;overflow:hidden}
body{position:relative;background:var(--white);font-family:"Roboto",Arial,sans-serif;color:var(--ink)}
.abs{position:absolute}

/* header */
.site-header{left:0;top:0;width:1200px;height:92px;background:var(--black)}
.brand{left:127px;top:16px;width:290px;height:60px;background:#2a2727;display:flex;flex-direction:column;align-items:center;justify-content:center;color:var(--white);font-weight:400}
.brand-name{font-size:29px;letter-spacing:4px;line-height:1}
.brand-sub{font-size:10px;letter-spacing:6px;margin-top:3px}
.main-nav a{position:absolute;top:41px;color:var(--white);font-size:14px;font-weight:500;text-decoration:none;white-space:nowrap}

/* hero */
.hero{left:0;top:92px;width:1200px;height:562px;background:linear-gradient(160deg,var(--hero-b),var(--hero-a) 55%,#7c7c7c)}
.hero-title{left:0;top:311px;width:1200px;text-align:center;color:var(--white);font-size:55px;font-weight:500;letter-spacing:-0.5px}
.hero-sub{left:0;top:386px;width:1200px;text-align:center;color:#eeeeee;font-size:17px;font-weight:400}
.hero-arrow{top:338px}

/* about */
.about{left:0;top:654px;width:1200px;height:359px;background:linear-gradient(100deg,var(--about-a),#1e1b17 45%,var(--about-b))}
.section-title{left:0;width:1200px;text-align:center;font-size:28px;font-weight:400}
.about-title{top:766px;color:var(--white)}
.about-text{left:145px;top:825px;width:910px;text-align:center;color:#e6e6e6;font-size:11px;line-height:19.5px;font-weight:400}
.btn-light{left:529px;top:930px;width:142px;height:36px;background:#e8e8e8;color:var(--ink);font-size:14px;display:flex;align-items:center;justify-content:center}

/* services */
.services{left:0;top:1013px;width:1200px;height:719px;background:var(--light)}
.services-title{top:1090px;color:var(--ink)}
.services-text{left:150px;top:1151px;width:900px;text-align:center;font-size:11.5px;line-height:19px;color:var(--ink)}
.service-card{top:1228px;width:289px}
.service-photo{width:289px;height:196px}
.service-name{margin-top:22px;font-size:19px;font-weight:400;color:var(--ink)}
.service-text{margin-top:14px;font-size:11px;line-height:19px;color:var(--grey)}
.btn-dark{margin-top:16px;width:93px;height:34px;background:var(--black);color:var(--white);font-size:11px;display:flex;align-items:center;justify-content:center}

/* contact */
.contact-panel{left:0;top:1732px;width:421px;height:511px;background:var(--black);color:var(--white)}
.contact-title{left:141px;top:1800px;font-size:29px;font-weight:400;color:var(--white)}
.person{left:198px;color:var(--white)}
.person-name{font-size:19px;font-weight:400}
.person-role{font-size:13px;font-weight:700;margin-top:1px}
.person-line{font-size:11.5px;margin-top:13px}
.map{left:421px;top:1732px;width:779px;height:511px;background:linear-gradient(135deg,#e0e0e0,var(--map) 50%,#c8c8c8)}

/* footer */
.site-footer{left:0;top:2243px;width:1200px;height:138px;background:var(--white)}
.footer-nav{left:145px;top:2295px;font-size:14px;color:#444;white-space:nowrap}
.footer-nav span{margin:0 19px;color:#444}
.copyright{left:145px;top:2331px;font-size:13.5px;color:#444}
.social{left:895px;top:2314px}
</style>
</head>
<body>

<header class="abs site-header">
  <div class="abs brand">
    <span class="brand-name">VELMARSH</span>
    <span class="brand-sub">GROUP</span>
  </div>
  <nav class="main-nav">
    <a style="left:583px">ABOUT US</a>
    <a style="left:691px">SERVICES</a>
    <a style="left:783px">SAFETY</a>
    <a style="left:857px">ENVIROMENT</a>
    <a style="left:968px">CONTACT US</a>
  </nav>
</header>

<section class="abs hero" role="img" aria-label="Black and white photo of a backhoe loader on a dirt work site"></section>
<h1 class="abs hero-title">WE ARE IN THE BUSINESS</h1>
<p class="abs hero-sub">OF ASBESTOS REMOVAL DEMOLITION EARTHWORKS AND TRANSPORT</p>
<svg class="abs hero-arrow" style="left:106px" width="20" height="38" viewBox="0 0 20 38"><polyline points="17,3 4,19 17,35" fill="none" stroke="#fcfcfc" stroke-width="3"/></svg>
<svg class="abs hero-arrow" style="left:1066px" width="20" height="38" viewBox="0 0 20 38"><polyline points="3,3 16,19 3,35" fill="none" stroke="#fcfcfc" stroke-width="3"/></svg>

<section class="abs about" role="img" aria-label="Dark photo of a large earthmoving machine wheel at dusk"></section>
<h2 class="abs section-title about-title">ABOUT US</h2>
<p class="abs about-text">Velmarsh Transport Pty Ltd was established by Director Daniel Velmarsh in 2002 with a focus providing services within the transport industry. Over time the company has developed and expanded to include the provision of Earthworks and Demolition. Daniel has over 10 years' experience working at all levels within these industries focusing primarily on Demolition and Earthworks in recent times. Velmarsh Transport and Demolition is built on core values of Service, Safety and Environment and are dedicated to delivering a quality, safe, cost effective, efficient and reliable service.</p>
<div class="abs btn-light">CONTACT US</div>

<section class="abs services"></section>
<h2 class="abs section-title services-title">SERVICES</h2>
<p class="abs services-text">Velmarsh Transport and Demolition offer an extensive range of services including Demolition, Earthworks and Asbestos Removal. We make it our business to consult with clients, assess their needs and tailor a complete solution. We pride ourselves on a professional approach and timely delivery of services.</p>

<article class="abs service-card" style="left:143px">
  <div class="service-photo" role="img" aria-label="Orange excavator demolishing a building" style="background:linear-gradient(180deg,#8fb0cf,#9b8a78 55%,#7a5c3e)"></div>
  <h3 class="service-name">DEMOLITION</h3>
  <p class="service-text">Velmarsh Transport and Demolition provide an extensive range of demolition services. A large amount of experience across a broad range of projects results in a dependable service and peace of mind for all clients.</p>
  <div class="btn-dark">Read More</div>
</article>

<article class="abs service-card" style="left:455px">
  <div class="service-photo" role="img" aria-label="Orange excavator on a rocky earthworks site" style="background:linear-gradient(180deg,#3d4856,#6f7680 55%,#8a8882)"></div>
  <h3 class="service-name">EARTHWORKS</h3>
  <p class="service-text">Velmarsh Transport and Demolition provide an extensive range of demolition services. A large amount of experience across a broad range of projects results in a dependable service and peace of mind for all clients.</p>
  <div class="btn-dark">Read More</div>
</article>

<article class="abs service-card" style="left:768px">
  <div class="service-photo" role="img" aria-label="Weathered corrugated asbestos roof sheeting under blue sky" style="background:linear-gradient(180deg,#4f86c8,#6c7c6a 35%,#6e6a62)"></div>
  <h3 class="service-name">ASBESTOS</h3>
  <p class="service-text">Asbestos is a naturally occurring silicate mineral made up of tiny fibres. When disturbed, it may produce a dust containing asbestos fibres. Breathing these fibres into the lungs may, in turn, cause a range of health</p>
  <div class="btn-dark">Read More</div>
</article>

<section class="abs contact-panel"></section>
<h2 class="abs contact-title">CONTACT US</h2>
<div class="abs person" style="top:1877px">
  <div class="person-name">Daniel Velmarsh</div>
  <div class="person-role">Director</div>
  <div class="person-line" style="margin-top:18px">0400 000 141</div>
  <div class="person-line">vtdemolition@example.com</div>
  <div class="person-line">PO Box 000 HARLOWE QLD 4000</div>
</div>
<div class="abs person" style="top:2070px">
  <div class="person-name">Megan Torlo</div>
  <div class="person-role">Administration</div>
  <div class="person-line" style="margin-top:18px">0400 000 294</div>
  <div class="person-line">vtdemolition@example.com</div>
  <div class="person-line">PO Box 000 HARLOWE QLD 4000</div>
</div>
<div class="abs map" role="img" aria-label="Greyscale street map showing the office location"></div>

<footer class="abs site-footer"></footer>
<nav class="abs footer-nav">ABOUT US<span>|</span>SERVICES<span>|</span>SAFETY<span>|</span>ENVIROMENT<span>|</span>CONTACT US</nav>
<p class="abs copyright">© 2015 COMPANY NAME | ALL RIGHTS RESERVED</p>
<svg class="abs social" width="164" height="30" viewBox="0 0 164 30" aria-hidden="true">
  <g fill="none" stroke="#b5b5b5" stroke-width="1.5">
    <circle cx="15" cy="15" r="13"/>
    <circle cx="48" cy="15" r="13"/>
    <circle cx="81" cy="15" r="13"/>
    <circle cx="114" cy="15" r="13"/>
    <circle cx="147" cy="15" r="13"/>
  </g>
</svg>

</body>
</html>
```